Stationary design for boutique production house

We need a stationary design for our production house, 'Lorno Productions' based in Singapore. We produce microfilms as well as podcasts, talkshows and events. Our logo is a stylized icon of our director, who is also the executive producer and host of our programs, Lorno. Our main company colors are Red, Black and white. We would like a clean, minimalist design incorporating our existing company logo that conveys a sense of urbanism and elegance.

Logo and font files are attached. f

Target Market(s)

We focus on lifestyle media rather than entertainment.

Industry/Entity Type

Boutique

Font styles to use
Serif
Sans Serif

Colors
ec1f27
ffffff
000000

Requirements
Must have
• Our company logo and at least one of our company colors.
Nice to have
• Our address and contact information.
Should not have
• Changes made to the company logo (using only certain parts of it is fine though)

```html
<!DOCTYPE html>
<html lang="en">
<head>
<meta charset="utf-8">
<title>Lorno Productions — Stationery</title>
<link rel="stylesheet" href="https://fonts.googleapis.com/css2?family=Exo+2:wght@400;500&family=Open+Sans:wght@400;600;700&display=swap">
<style>
:root{
  --red:#d72d33;
  --ink:#333335;
  --paper:#ffffff;
  --ground:#ececec;
  --text:#555;
  --sans:"Open Sans", Arial, sans-serif;
  --wide:"Exo 2", Arial, sans-serif;
}
*{margin:0;padding:0;box-sizing:border-box}
html,body{width:1200px;height:937px;overflow:hidden;background:var(--ground)}
.canvas{position:relative;width:1200px;height:937px}
.piece{position:absolute;background:var(--paper);overflow:hidden}
.brand{display:flex;flex-direction:column;align-items:center;text-align:center}
.brand-dot{display:block;border-radius:50%;background:var(--red)}
.brand-name{font-family:var(--sans);font-weight:600;color:var(--ink);line-height:1.2;letter-spacing:.04em}
.icon{display:block;fill:none;stroke:currentColor;stroke-width:1.4}
.web{font-family:var(--wide);color:var(--ink);letter-spacing:.14em;white-space:nowrap}

/* Letterhead */
.letterhead{left:184px;top:66px;width:389px;height:546px}
.letterhead .sidebar{position:absolute;left:0;top:0;width:28px;height:100%;background:var(--ink)}
.letterhead .brand{position:absolute;left:36px;top:30px;width:76px;gap:10px}
.letterhead .brand-dot{width:40px;height:40px}
.letterhead .brand-name{font-size:10px}
.letter{position:absolute;left:37px;top:140px;width:300px;font-family:var(--sans);font-size:5.6px;line-height:1.55;color:var(--text)}
.letter p{margin-bottom:12px}
.letter .date{margin-bottom:6px}
.letter .salute{margin-bottom:6px}
.letter strong{color:#333}
.signature{width:40px;height:12px;background:linear-gradient(90deg,#555,#999);opacity:.5;margin:4px 0 10px;border-radius:6px}
.contact-rail{position:absolute;left:0;top:455px;width:120px}
.contact-row{display:flex;align-items:center;gap:6px;margin-bottom:8px;font-family:var(--sans);font-size:4.6px;line-height:1.4;color:var(--text)}
.contact-row .bubble{width:14px;height:14px;border-radius:50%;background:var(--ink);color:#fff;display:flex;align-items:center;justify-content:center;margin-left:-1px;border:1px solid #fff}
.contact-row .bubble svg{width:8px;height:8px}
.contact-row .info{margin-left:14px;text-align:right;min-width:40px}

/* Folder */
.folder{left:636px;top:40px;width:458px;height:576px}
.folder .strip{position:absolute;left:0;top:0;width:41px;height:100%;background:var(--red)}
.folder .brand{position:absolute;left:41px;right:0;top:190px;gap:28px}
.folder .brand-dot{width:120px;height:120px}
.folder .brand-name{font-size:28px}
.folder .badge{position:absolute;left:28px;top:526px;width:26px;height:26px;border-radius:50%;background:var(--paper);color:var(--ink);display:flex;align-items:center;justify-content:center;box-shadow:0 0 0 3px var(--red)}
.folder .badge svg{width:16px;height:16px}
.folder .web{position:absolute;left:60px;top:532px;font-size:12px}

/* Business cards */
.card{width:176px;height:100px}
.card-front{left:45px;top:658px}
.card-front .dark{position:absolute;left:0;top:0;width:100%;height:100%}
.card-front .details{position:absolute;left:6px;top:12px;width:56px;text-align:right;font-family:var(--sans);font-size:4.4px;line-height:1.45;color:#eee}
.card-front .details div{margin-bottom:8px}
.card-front .rail{position:absolute;left:68px;top:10px;color:#fff}
.card-front .rail span{display:flex;width:12px;height:12px;border-radius:50%;border:1px solid #fff;background:var(--ink);align-items:center;justify-content:center;margin-bottom:11px}
.card-front .rail svg{width:7px;height:7px}
.card-front .brand{position:absolute;left:100px;top:8px;width:70px;gap:5px}
.card-front .brand-dot{width:26px;height:26px}
.card-front .brand-name{font-size:6px}
.card-front .person{position:absolute;right:8px;top:76px;font-family:var(--sans);font-size:6.6px;line-height:1.2;color:var(--ink);text-align:right}
.card-front .person b{font-weight:400;letter-spacing:.03em}
.card-back{left:45px;top:785px;height:97px}
.card-back .brand{position:absolute;left:0;right:0;top:18px;gap:6px}
.card-back .brand-dot{width:32px;height:32px}
.card-back .brand-name{font-size:7px}

/* Envelopes */
.envelope-front{left:265px;top:672px;width:402px;height:209px}
.envelope-front .strip{position:absolute;left:0;top:0;width:22px;height:100%;background:var(--ink)}
.envelope-front .badge{position:absolute;left:10px;top:175px;width:20px;height:20px;border-radius:50%;background:var(--ink);color:#fff;display:flex;align-items:center;justify-content:center}
.envelope-front .badge svg{width:12px;height:12px}
.envelope-front .brand{position:absolute;left:30px;top:20px;width:76px;gap:8px}
.envelope-front .brand-dot{width:48px;height:48px}
.envelope-front .brand-name{font-size:9px}
.envelope-front .web{position:absolute;left:38px;top:180px;font-size:9px}
.envelope-back{left:737px;top:672px;width:431px;height:209px}
.envelope-back .flap{position:absolute;left:0;top:0;width:100%;height:71px;background:var(--ink);border-radius:0 0 44px 44px}
.envelope-back .web{position:absolute;left:0;right:0;top:28px;text-align:center;font-size:14px;color:#fff;letter-spacing:.2em}
</style>
</head>
<body>
<div class="canvas">

  <!-- Letterhead -->
  <section class="piece letterhead">
    <div class="sidebar"></div>
    <div class="brand">
      <span class="brand-dot"></span>
      <span class="brand-name">Lorno Productions</span>
    </div>
    <div class="letter">
      <p class="date">July 2, 2012</p>
      <p class="salute"><strong>Dear Client,</strong><br>12 Keong Saik Road, Singapore</p>
      <p>Thank you for choosing Lorno Productions for your upcoming lifestyle series. We have reviewed the outline you shared and prepared a schedule for scripting, casting and filming. Our team will handle location scouting, sound and lighting, and we will share first cuts for your review within three weeks of the shoot.</p>
      <p>Please confirm the proposed dates at your earliest convenience so that we can reserve the studio and crew for the sessions.</p>
      <p style="margin-top:22px">We look forward to working with you on this project. Should you have any questions about budgets, talent or post production, our office is open on weekdays and our producers are always glad to talk through ideas, timelines and the creative direction of each episode before work begins.</p>
      <p style="margin-bottom:2px">Best Regards,</p>
      <div class="signature" role="img" aria-label="Handwritten signature"></div>
      <p><strong>Daniel Tan</strong><br>Director<br><br>12 Keong Saik Road, Singapore</p>
    </div>
    <div class="contact-rail">
      <div class="contact-row">
        <span class="bubble"><svg class="icon" viewBox="0 0 16 16"><path d="M4 2l3 3-2 2c1 2 2 3 4 4l2-2 3 3-2 2C7 14 2 9 2 4z"/></svg></span>
        <span class="info">+65 6123 4567<br>+65 6123 4568</span>
      </div>
      <div class="contact-row">
        <span class="bubble"><svg class="icon" viewBox="0 0 16 16"><path d="M8 15s-5-5-5-9a5 5 0 0110 0c0 4-5 9-5 9z"/><circle cx="8" cy="6" r="1.6"/></svg></span>
        <span class="info">12 Keong Saik Road<br>Chinatown<br>Singapore</span>
      </div>
      <div class="contact-row">
        <span class="bubble"><svg class="icon" viewBox="0 0 16 16"><circle cx="8" cy="8" r="6"/><path d="M2 8h12M8 2c3 3 3 9 0 12M8 2c-3 3-3 9 0 12"/></svg></span>
        <span class="info">hello@lornoproductions.sg<br>studio@lornoproductions.sg</span>
      </div>
    </div>
  </section>

  <!-- Presentation folder -->
  <section class="piece folder">
    <div class="strip"></div>
    <div class="brand">
      <span class="brand-dot"></span>
      <span class="brand-name">Lorno Productions</span>
    </div>
    <span class="badge"><svg class="icon" viewBox="0 0 16 16"><circle cx="8" cy="8" r="6"/><path d="M2 8h12M8 2c3 3 3 9 0 12M8 2c-3 3-3 9 0 12"/></svg></span>
    <span class="web">www.lornoproductions.sg</span>
  </section>

  <!-- Business card, front -->
  <section class="piece card card-front">
    <svg class="dark" viewBox="0 0 176 100" preserveAspectRatio="none"><path d="M0 0H76C82 8 82 18 76 26C70 34 70 42 76 50C82 58 82 68 76 76V86H100V100H0Z" fill="var(--ink)"/></svg>
    <div class="details">
      <div>+65 6123 4567<br>+65 6123 4568</div>
      <div>12 Keong Saik Road<br>Chinatown<br>Singapore</div>
      <div>hello@lornoproductions.sg<br>studio@lornoproductions.sg</div>
    </div>
    <div class="rail">
      <span><svg class="icon" viewBox="0 0 16 16"><path d="M4 2l3 3-2 2c1 2 2 3 4 4l2-2 3 3-2 2C7 14 2 9 2 4z"/></svg></span>
      <span><svg class="icon" viewBox="0 0 16 16"><path d="M8 15s-5-5-5-9a5 5 0 0110 0c0 4-5 9-5 9z"/></svg></span>
      <span><svg class="icon" viewBox="0 0 16 16"><circle cx="8" cy="8" r="6"/><path d="M2 8h12M8 2v12"/></svg></span>
    </div>
    <div class="brand">
      <span class="brand-dot"></span>
      <span class="brand-name">Lorno Productions</span>
    </div>
    <div class="person"><b>MARCUS LEE</b><br>Managing Director</div>
  </section>

  <!-- Business card, back -->
  <section class="piece card card-back">
    <div class="brand">
      <span class="brand-dot"></span>
      <span class="brand-name">Lorno Productions</span>
    </div>
  </section>

  <!-- Envelope, front -->
  <section class="piece envelope-front">
    <div class="strip"></div>
    <span class="badge"><svg class="icon" viewBox="0 0 16 16"><circle cx="8" cy="8" r="6"/><path d="M2 8h12M8 2c3 3 3 9 0 12M8 2c-3 3-3 9 0 12"/></svg></span>
    <div class="brand">
      <span class="brand-dot"></span>
      <span class="brand-name">Lorno Productions</span>
    </div>
    <span class="web">www.lornoproductions.sg</span>
  </section>

  <!-- Envelope, back -->
  <section class="piece envelope-back">
    <div class="flap"><div class="web">www.lornoproductions.sg</div></div>
  </section>

</div>
</body>
</html>
```